wealth management firm, professional group, new model

we have a logo that works but we need a card, white background using our colors...clean look

our tag line if can be used in

Steady Counsel for Lasting Wealth

```html
<!DOCTYPE html>
<html lang="en">
<head>
<meta charset="UTF-8">
<title>Varco Wealth Partners – Business Card</title>
<link href="https://fonts.googleapis.com/css2?family=Montserrat:wght@400;500;600&display=swap" rel="stylesheet">
<style>
  :root {
    --backdrop: #e8e8e7;
    --paper: #f8f8f6;
    --navy: #1b2d51;
    --ink: #2e4062;
    --ink-soft: #4a5670;
    --rule: #7d8aa3;
    --on-navy: #e9edf4;
    --on-navy-soft: #5a6f96;
  }
  * { margin: 0; padding: 0; box-sizing: border-box; }
  html, body {
    width: 1200px; height: 800px; overflow: hidden;
    background: var(--backdrop);
    font-family: "Montserrat", sans-serif;
  }
  .canvas { position: relative; width: 1200px; height: 800px; }
  .card {
    position: absolute; left: 405px; width: 400px; height: 260px;
  }
  .card--front { top: 113px; background: var(--paper); color: var(--ink); }
  .card--back { top: 438px; background: var(--navy); }

  .wordmark {
    position: absolute; display: flex; align-items: center; gap: 9px;
    font-weight: 500; white-space: nowrap;
  }
  .card--front .wordmark {
    right: 42px; top: 68px; font-size: 13px; letter-spacing: 2.6px; color: var(--ink);
  }
  .card--back .wordmark {
    left: 0; right: 0; justify-content: center; top: 100px;
    font-size: 17px; letter-spacing: 3.6px; color: var(--on-navy-soft);
  }
  .wordmark__dot { width: 9px; height: 9px; border-radius: 50%; background: currentColor; flex: none; }

  .person { position: absolute; left: 46px; top: 132px; }
  .person__name { font-size: 14px; font-weight: 600; letter-spacing: 0.1px; line-height: 1.05; }
  .person__role { font-size: 11.5px; font-weight: 400; color: var(--ink-soft); line-height: 1.2; }

  .divider {
    position: absolute; left: 46px; top: 170px; width: 308px; height: 1px; background: var(--rule);
  }
  .contact {
    position: absolute; left: 46px; top: 180px; list-style: none;
    font-size: 10.5px; color: var(--ink-soft); line-height: 15.5px;
  }
  .contact__row { display: flex; align-items: center; gap: 4px; white-space: nowrap; }
  .contact__item { display: inline-flex; align-items: center; gap: 4px; margin-right: 4px; }
  .icon { width: 10px; height: 10px; fill: none; stroke: var(--ink); stroke-width: 1.3; }
  .icon--solid { fill: var(--ink); stroke: none; }

  .tagline {
    position: absolute; left: 0; right: 0; top: 216px; text-align: center;
    font-size: 9px; font-weight: 500; letter-spacing: 1.6px; color: var(--on-navy);
  }
</style>
</head>
<body>
<main class="canvas">
  <section class="card card--front" aria-label="Card front">
    <div class="wordmark"><span class="wordmark__dot"></span>VARCO WEALTH PARTNERS</div>

    <div class="person">
      <p class="person__name">DANIEL R. HALE</p>
      <p class="person__role">Brand Manager</p>
    </div>

    <div class="divider"></div>

    <ul class="contact">
      <li class="contact__row">Via Corsini 14 20121 Milano, Italy</li>
      <li class="contact__row">
        <span class="contact__item">
          <svg class="icon icon--solid" viewBox="0 0 24 24" aria-hidden="true"><path d="M6.6 10.8a15.1 15.1 0 0 0 6.6 6.6l2.2-2.2c.3-.3.7-.4 1-.2 1.1.4 2.300.6 3.6.6.6 0 1 .4 1 1V20c0 .6-.4 1-1 1A17 17 0 0 1 3 4c0-.6.4-1 1-1h3.5c.6 0 1 .4 1 1 0 1.3.2 2.5.6 3.6.1.3 0 .7-.2 1z"/></svg>
          +39.340.555.0182
        </span>
        <span class="contact__item">
          <svg class="icon" viewBox="0 0 24 24" aria-hidden="true"><rect x="2" y="5" width="20" height="14"/><path d="M2 5l10 8 10-8M2 19l7-7M22 19l-7-7"/></svg>
          info@varcomail.com
        </span>
      </li>
      <li class="contact__row">
        <svg class="icon" viewBox="0 0 24 24" aria-hidden="true"><circle cx="12" cy="12" r="10"/><ellipse cx="12" cy="12" rx="4.5" ry="10"/><path d="M2 12h20M4 7h16M4 17h16"/></svg>
        www.varcoweb.com
      </li>
    </ul>
  </section>

  <section class="card card--back" aria-label="Card back">
    <div class="wordmark"><span class="wordmark__dot"></span>VARCO WEALTH PARTNERS</div>
    <p class="tagline">STEADY COUNSEL FOR LASTING WEALTH</p>
  </section>
</main>
</body>
</html>
```